Weightloss company needs Business Card

We want a business card that is clean and professional, yet portrays that we are a friendly, innovative, and versatile program designed to fit the needs of our clients.
I would like there to be 2 sides, one side having an appointment card, and the other side containing the logo and business information. There can be decorations on both sides. The logo is attached.

Target Market(s)

Men and women 40-60

Industry/Entity Type

Business

Contact Information for Business Card

Font styles to use
Sans Serif

Requirements
Must have
• The logo, space for business information
Nice to have
• The colors in the logo
Should not have
• No pictures of people or food

```html
<!DOCTYPE html>
<html lang="en">
<head>
<meta charset="utf-8">
<title>Renew Turn Wellness – Business Card</title>
<link rel="stylesheet" href="https://fonts.googleapis.com/css2?family=Open+Sans:wght@400;600;700&display=swap">
<style>
  :root {
    --brand-red: #e41c38;
    --brand-blue: #35b3e6;
    --ink: #1d1d1f;
    --rule: #555;
    --card: #ffffff;
    --backdrop: #e6e7ea;
    --ghost: #eaf6fc;
  }
  * { box-sizing: border-box; margin: 0; padding: 0; }
  html, body { width: 1200px; height: 900px; overflow: hidden; }
  body {
    background: var(--backdrop);
    font-family: "Open Sans", Arial, sans-serif;
    color: var(--ink);
    position: relative;
  }
  .card {
    position: absolute;
    width: 540px;
    height: 310px;
    background: var(--card);
    border-radius: 22px;
    overflow: hidden;
    box-shadow: 0 10px 28px rgba(0,0,0,.18);
  }
  .card--appointment { left: 70px; top: 100px; }
  .card--contact { left: 590px; top: 480px; }

  .wordmark {
    position: absolute;
    top: 36px;
    right: 34px;
    display: flex;
    align-items: center;
    gap: 10px;
    font-weight: 700;
    font-size: 24px;
    color: var(--brand-red);
    letter-spacing: .2px;
  }
  .wordmark__dot {
    width: 14px; height: 14px;
    border-radius: 50%;
    background: var(--brand-red);
  }

  /* appointment side */
  .appointment {
    position: absolute;
    left: 40px;
    right: 40px;
    top: 140px;
  }
  .appointment__title {
    color: var(--brand-red);
    font-size: 14px;
    font-weight: 400;
    letter-spacing: .4px;
    margin-bottom: 10px;
  }
  .appointment__field {
    display: flex;
    align-items: flex-end;
    gap: 10px;
    font-size: 14px;
    height: 40px;
  }
  .appointment__line {
    flex: 1;
    border-bottom: 1px solid var(--rule);
    height: 1px;
    margin-bottom: 5px;
  }

  /* contact side */
  .ghost-ring {
    position: absolute;
    left: 30px; top: 40px;
    width: 250px; height: 250px;
    border-radius: 50%;
    border: 12px solid var(--ghost);
  }
  .person {
    position: absolute;
    left: 30px;
    top: 60px;
  }
  .person__name {
    color: var(--brand-red);
    font-size: 22px;
    font-weight: 400;
    text-transform: uppercase;
    letter-spacing: .3px;
  }
  .person__role {
    color: var(--brand-blue);
    font-size: 13px;
    font-weight: 600;
    text-transform: uppercase;
    letter-spacing: .5px;
  }
  .contact-list {
    position: absolute;
    right: 30px;
    top: 110px;
    list-style: none;
    font-size: 13px;
  }
  .contact-list li {
    display: flex;
    align-items: center;
    gap: 8px;
    line-height: 20px;
  }
  .contact-list svg { width: 12px; height: 12px; flex: none; }
  .band { position: absolute; left: 0; top: 0; }
  .address {
    position: absolute;
    left: 30px;
    bottom: 10px;
    color: #fff;
    font-size: 14px;
    line-height: 18px;
  }
</style>
</head>
<body>

<section class="card card--appointment" aria-label="Appointment side">
  <div class="wordmark"><span class="wordmark__dot"></span>Renew Turn Wellness</div>
  <div class="appointment">
    <h2 class="appointment__title">APPOINTMENT</h2>
    <div class="appointment__field"><span>Name:</span><span class="appointment__line"></span></div>
    <div class="appointment__field"><span>Date:</span><span class="appointment__line"></span></div>
    <div class="appointment__field"><span>Time:</span><span class="appointment__line"></span></div>
  </div>
</section>

<section class="card card--contact" aria-label="Contact side">
  <div class="ghost-ring"></div>
  <svg class="band" width="540" height="310" viewBox="0 0 540 310" aria-hidden="true">
    <polygon points="400,205 540,205 540,235 470,235" fill="#111"/>
    <polygon points="0,252 340,252 390,205 470,235 540,235 540,310 0,310" fill="var(--brand-red)"/>
  </svg>
  <div class="wordmark"><span class="wordmark__dot"></span>Renew Turn Wellness</div>
  <div class="person">
    <h1 class="person__name">Marcus Hale</h1>
    <p class="person__role">Director</p>
  </div>
  <ul class="contact-list">
    <li>
      <svg viewBox="0 0 24 24"><path fill="var(--brand-red)" d="M6.6 10.8a15 15 0 0 0 6.6 6.6l2.2-2.2a1 1 0 0 1 1-.25 11.4 11.4 0 0 0 3.6.57 1 1 0 0 1 1 1V20a1 1 0 0 1-1 1A17 17 0 0 1 3 4a1 1 0 0 1 1-1h3.5a1 1 0 0 1 1 1c0 1.25.2 2.45.57 3.57a1 1 0 0 1-.25 1z"/></svg>
      +330 1875-4402
    </li>
    <li>
      <svg viewBox="0 0 24 24"><rect x="2.5" y="5" width="19" height="14" rx="1.5" fill="none" stroke="var(--brand-red)" stroke-width="2.2"/><path d="M3 6l9 7 9-7" fill="none" stroke="var(--brand-red)" stroke-width="2.2"/></svg>
      hello@renewturnwellness.com
    </li>
    <li>
      <svg viewBox="0 0 24 24"><circle cx="12" cy="12" r="9.5" fill="none" stroke="var(--brand-red)" stroke-width="2"/><path d="M2.5 12h19M12 2.5c3 3 3 16 0 19M12 2.5c-3 3-3 16 0 19" fill="none" stroke="var(--brand-red)" stroke-width="1.6"/></svg>
      www.renewturnwellness.com
    </li>
  </ul>
  <address class="address" style="font-style:normal">Palm Avenue, 21530<br>Jeddah, Saudi Arabia</address>
</section>

</body>
</html>
```